New website for a business that provides behaviour analysis

A new website that details the services that are provided around behaviour analysis for people with a disability through QPKV. There also needs to incorporate an about us and a staff page, Plus a referral form that is a google doc.
The business already has a web address that needs to be tailored.
Soft colours are preferred.
Do not have lots of pictures, keep them minimal.
A logo for the business is also needed to be incorporated, and this is a separate project that can be awarded to the website winner.
Website needs to be able to be used on WIX who will be the host for the design.

Target Market(s)

QPKV clients requiring behaviour support clician

Industry/Entity Type

Clinical behaviour support and analysis

Colors
00AB8E
00BBA5
67D7C9
C6EFE9
E9F9F6

Requirements
Must have
• Soft colours, preferable pale turquoise, minimal pictures, clean, sophisticated and classical look

```html
<!DOCTYPE html>
<html lang="en">
<head>
<meta charset="utf-8">
<title>Tendwell – Behaviour Support</title>
<link href="https://fonts.googleapis.com/css2?family=Montserrat:wght@500;600;700&family=Lato:wght@400;700&family=Inter:wght@400;500;600&display=swap" rel="stylesheet">
<style>
:root{
  --green:#00ab8e;
  --mint:#13e0b0;
  --sky:#dbeafa;
  --panel:#f0f0f0;
  --foot:#e6f2ef;
  --ink:#1d1d1f;
  --body:#4a4a4a;
  --muted:#9a9a9a;
  --line:#dcdcdc;
  --white:#fff;
  --ring:#7fd8c8;
  --dot-blue:#1f5fc4;
  --dot-green:#1fcf9f;
}
*{margin:0;padding:0;box-sizing:border-box}
html,body{width:821px;height:1200px;overflow:hidden;background:var(--white)}
body{position:relative;font-family:'Lato',sans-serif;color:var(--ink)}
.abs{position:absolute}
.topbar{left:0;top:0;width:821px;height:26px;background:var(--green);color:var(--white);font:400 7px 'Inter',sans-serif}
.topbar span{position:absolute;top:9px}
.topbar .dot{position:absolute;top:6px;width:14px;height:14px;border-radius:50%;background:var(--dot-blue)}
.brand{font:500 14px 'Inter',sans-serif;color:var(--ink);display:flex;align-items:center;gap:5px}
.brand i{display:block;width:18px;height:18px;border-radius:50%;background:var(--green)}
.nav a{position:absolute;top:53px;font:400 8px 'Inter',sans-serif;color:var(--ink);text-decoration:none}
.nav a.active{color:var(--green)}
.nav .underline{position:absolute;left:298px;top:86px;width:31px;height:1.5px;background:var(--green)}
.btn{display:flex;align-items:center;justify-content:center;font:500 7px 'Inter',sans-serif;color:var(--white);background:var(--green);text-decoration:none}
.btn.mint{background:var(--mint);color:var(--ink)}
.hero-band{left:37px;top:88px;width:746px;height:184px;background:var(--sky)}
.card{left:154px;top:130px;width:513px;height:223px;background:var(--panel)}
.photo{background:linear-gradient(160deg,#c9cdc9,#e8e6e2 60%,#d7d8d6)}
.doc-name{left:355px;top:162px;font:700 18px 'Montserrat',sans-serif}
.doc-role{left:355px;top:186px;font:600 9px 'Montserrat',sans-serif;color:var(--green)}
.doc-text{left:355px;top:207px;width:290px;font:400 6.5px/10px 'Lato',sans-serif;color:var(--body)}
.contact .ring{position:absolute;width:25px;height:25px;border:1px solid var(--ring);border-radius:50%}
.contact .label{position:absolute;font:700 5.5px 'Lato',sans-serif}
.contact .value{position:absolute;font:700 8.5px 'Lato',sans-serif}
.form-panel{left:154px;top:418px;width:295px;height:447px;background:var(--panel)}
.form-title{left:188px;top:451px;font:600 18px 'Montserrat',sans-serif}
.form-text{left:188px;top:483px;width:225px;font:400 6.5px/10px 'Lato',sans-serif;color:var(--body)}
.field{left:188px;width:226px;height:26px;background:var(--white);border:1px solid var(--line);font:400 6.5px 'Lato',sans-serif;color:var(--muted);padding:10px 0 0 13px}
.hours-photo{left:458px;top:418px;width:209px;height:219px;background:linear-gradient(165deg,#b9d3e8,#dfe8ef 45%,#9db0c0)}
.hours{left:492px;top:480px;width:141px;height:94px;background:rgba(255,255,255,.78);text-align:center}
.hours .kicker{margin-top:22px;font:500 6px 'Montserrat',sans-serif;letter-spacing:3px}
.hours h3{font:600 13px 'Montserrat',sans-serif;margin-top:5px}
.hours p{font:400 6.5px/10px 'Lato',sans-serif;color:var(--body);margin-top:3px}
.ask{left:458px;top:646px;width:209px;height:219px;background:var(--green);color:var(--white);text-align:center}
.ask h2{margin-top:44px;font:500 22px/28px 'Montserrat',sans-serif}
.ask p{margin:11px auto 0;width:110px;font:400 6.5px/10px 'Lato',sans-serif}
.ask .btn{margin:15px auto 0;width:100px;height:26px}
.footer{left:40px;top:935px;width:741px;height:237px;background:var(--foot)}
.foot-contact{position:absolute;top:987px;font:400 6.5px 'Lato',sans-serif;color:var(--body)}
.foot-dot{position:absolute;top:978px;width:18px;height:18px;border-radius:50%;background:var(--dot-green)}
.social{position:absolute;top:982px;width:10px;height:10px;border-radius:50%;border:1.4px solid var(--green)}
.quote{left:154px;top:1030px;width:175px;font:600 12.5px/18px 'Montserrat',sans-serif}
.col h4{font:500 8.5px 'Montserrat',sans-serif;margin-bottom:7px}
.col a{display:block;font:400 6.5px/13.7px 'Lato',sans-serif;color:var(--body);text-decoration:none}
.col p{font:400 6.5px/10px 'Lato',sans-serif;color:var(--body)}
.copy{left:0;top:1184px;width:821px;text-align:center;font:400 6.5px 'Lato',sans-serif;color:var(--body)}
</style>
</head>
<body>

<header>
  <div class="abs topbar">
    <span style="left:154px">Welcome to Tendwell. We provide behaviour support services</span>
    <i class="dot" style="left:475px"></i><span style="left:494px">(555) 210 - 4390</span>
    <i class="dot" style="left:592px"></i><span style="left:611px">(555) 210 - 4390</span>
  </div>
  <div class="abs brand" style="left:156px;top:49px"><i></i>Tendwell</div>
  <nav class="nav">
    <a class="active" style="left:303px" href="#">Home</a>
    <a style="left:344px" href="#">About</a>
    <a style="left:385px" href="#">Service</a>
    <a style="left:432px" href="#">Pages <span style="color:var(--green)">●</span></a>
    <a style="left:474px" href="#">Contact Us</a>
    <span class="underline"></span>
  </nav>
  <a class="abs btn mint" style="left:587px;top:45px;width:80px;height:26px;font-size:7.5px" href="#">Appointment</a>
</header>

<section>
  <div class="abs hero-band"></div>
  <div class="abs card"></div>
  <div class="abs photo" style="left:167px;top:142px;width:166px;height:199px" role="img" aria-label="Portrait photo of the behaviour support clinician"></div>
  <h1 class="abs doc-name">Dr. Elena Marsh</h1>
  <div class="abs doc-role">Behaviour Analyst</div>
  <p class="abs doc-text">Elena leads our clinical team, building positive behaviour support plans with QPKV participants, families and carers. Her practice focuses on understanding the reasons behind behaviour and on calm, practical strategies that improve daily life.</p>
  <div class="contact">
    <span class="ring" style="left:355px;top:253px"></span>
    <svg class="abs" style="left:362px;top:260px" width="11" height="11" viewBox="0 0 24 24" fill="none" stroke="#00ab8e" stroke-width="1.6"><path d="M5 3h4l2 5-3 2a12 12 0 0 0 6 6l2-3 5 2v4a2 2 0 0 1-2 2A18 18 0 0 1 3 5a2 2 0 0 1 2-2z"/></svg>
    <span class="label" style="left:386px;top:256px">CALL NOW:</span>
    <span class="value" style="left:386px;top:265px">(+00) 555 - 0142 - 300</span>
    <span class="ring" style="left:494px;top:253px"></span>
    <svg class="abs" style="left:501px;top:260px" width="11" height="11" viewBox="0 0 24 24" fill="none" stroke="#00ab8e" stroke-width="1.6"><circle cx="12" cy="12" r="4"/><path d="M16 8v5a3 3 0 0 0 6 0v-1a10 10 0 1 0-4 8"/></svg>
    <span class="label" style="left:525px;top:256px">EMAIL NOW:</span>
    <span class="value" style="left:525px;top:265px">info@tendwellclinic.com</span>
  </div>
  <a class="abs btn" style="left:355px;top:295px;width:80px;height:25px" href="#">Discover Now</a>
</section>

<section>
  <div class="abs form-panel"></div>
  <h2 class="abs form-title">Book an appoinment</h2>
  <p class="abs form-text">Tell us a little about the person you support and we will contact you to arrange a first meeting.</p>
  <div class="abs field" style="top:514px">Name</div>
  <div class="abs field" style="top:548px">Email</div>
  <div class="abs field" style="top:583px">Phone</div>
  <div class="abs field" style="top:617px">Service Needed</div>
  <div class="abs field" style="top:651px">Date
    <svg class="abs" style="right:8px;top:7px" width="11" height="11" viewBox="0 0 24 24" fill="none" stroke="#b5b5b5" stroke-width="1.5"><rect x="3" y="5" width="18" height="16" rx="2"/><path d="M3 10h18M8 3v4M16 3v4"/></svg>
  </div>
  <div class="abs field" style="top:685px">Choose Clinician
    <svg class="abs" style="right:8px;top:9px" width="7" height="7" viewBox="0 0 10 10"><circle cx="5" cy="5" r="5" fill="#9a9a9a"/><path d="M3 4.5l2 2 2-2" stroke="#fff" fill="none"/></svg>
  </div>
  <div class="abs field" style="top:719px;height:77px">Message...</div>
  <a class="abs btn" style="left:188px;top:804px;width:226px;height:26px" href="#">Booking Now</a>

  <div class="abs hours-photo" role="img" aria-label="Photo of a clinician reading notes in a corridor"></div>
  <div class="abs hours">
    <div class="kicker">TIME</div>
    <h3>Working Hours</h3>
    <p>Sunday To Friday 9.00 am - 10.00 pm<br>Saturday Closed</p>
  </div>
  <div class="abs ask">
    <h2>Didn’t Find a Question?</h2>
    <p>Send us your question about QPKV behaviour support and we will reply soon.</p>
    <a class="btn mint" href="#">More Questions</a>
  </div>
</section>

<footer>
  <div class="abs footer"></div>
  <div class="abs brand" style="left:156px;top:978px"><i></i>Tendwell Care</div>
  <i class="foot-dot" style="left:384px"></i><span class="foot-contact" style="left:406px">(+00) 555 - 0142 - 300</span>
  <i class="foot-dot" style="left:498px"></i><span class="foot-contact" style="left:520px">support@tendwellclinic.com</span>
  <i class="social" style="left:615px"></i>
  <i class="social" style="left:636px"></i>
  <i class="social" style="left:657px"></i>
  <p class="abs quote">“Clear, Caring Support That Helps People Live Well, Every Single Day</p>
  <div class="abs col" style="left:351px;top:1028px">
    <h4>Explore</h4>
    <a href="#">Home</a><a href="#">Services</a><a href="#">About us</a><a href="#">Our Staff</a><a href="#">Referral</a>
  </div>
  <div class="abs col" style="left:429px;top:1028px">
    <h4>Utility Pages</h4>
    <a href="#">Style Guide</a><a href="#">Changelog</a><a href="#">Licenses</a><a href="#">Protected Page</a><a href="#">404 Page</a>
  </div>
  <div class="abs col" style="left:527px;top:1028px;width:140px">
    <h4>Book an appointment</h4>
    <p>Leave your email and our team will be in touch with you shortly</p>
  </div>
  <div class="abs field" style="left:527px;top:1072px;width:140px;border:none;padding-left:11px">your email address</div>
  <a class="abs btn" style="left:527px;top:1104px;width:59px;height:26px" href="#">Submit</a>
  <p class="abs copy">Copyright © Tendwell Care</p>
</footer>

</body>
</html>
```